Hardcore nerd needs to stand out in a sea of dull Defence business cards

Wombarra Devices is a new Australian consulting engineering company that turns research and theory into practical systems. No evangelistic fluff, just mathematics and physics into electronic and optical circuits for consumer products, scientific research or Defence applications.

We already have a recognised logo (provided) which is often dark blue/black on a light background but we're open to other combinations. (Us engineers tend to have limited aesthetic imagination :)

Some of our recent products have included:
* Instrumentation for electrical testing,
* Radar jammers,
* GPS antenna design,
* Satellite tracking systems,
* High power lasers

We're open to both single and double-sided designs - happy to be convinced either way.

P.S. Another group is working on the web page, so - alas - our web site is currently of no use for images/ideas...

Target Market(s)

Engineering managers,
Scientists

Contact Information for Business Card

Dr Colin Harte
R&D Engineer

colin@wombarradevices.com.au
0427 563 710

PO Box XXX (to be confirmed)
Kelsby ACT 2917
Australia

Font styles to use
Serif
Sans Serif

Colors

Designer to choose colors to be used in the design.

Requirements
Must have
• My contact details!
• I've had many (great) "bold and plain" designs submitted already, so feel free to be artistically creative :)
• Happy to take advice re fonts/colours/printability etc.
Nice to have
• I'm not sure if "lists" are more at home on a CV than a business card, but representative services include:
• Applied electromagnetics
• RF and high speed electronics
• Signal and image processing
• Electro-optical and laser systems
• Concept-to-prototype design services
• If you're considering double sided cards, then often measuring/alignment grids/rulers feature on the back of similar cards.
• e.g. https://www.veltranoptics.example/newgrouppage9.cfm?objectgroup_id=4183
• https://www.veltranoptics.example/newgrouppage9.cfm?objectgroup_ID=4185
• ..or even a "Smith chart" (google will return lots)
• Generic images to represent a capability might work - googling images associated with keyword for each of these areas might help:
• - "passive radar", "phased array", "fdtd", "vircator"
• RF and high speed electronic design
• - "smith chart", "microstrip circuits", "dimensioned drawing", "electronic schematic"
• - "dft", "iir filter"
• - "optical cavity". "laser energy level diagram"
• Background/watermarked images outlines/wireframes/schematics would probably look OK.
Should not have
• If a list of projects/services is provided, it is important not to make the client feel that this is "all" the company can do. Engineering design is a creative discipline (like graphics :)
• Please, no stock "military" snaps like planes, missiles, etc!

```html
<!DOCTYPE html>
<html lang="en">
<head>
<meta charset="utf-8">
<title>Wombarra Devices — Business Card</title>
<link rel="stylesheet" href="https://fonts.googleapis.com/css2?family=Montserrat:wght@400;500;700;800&display=swap">
<style>
  :root {
    --backdrop: #e7e6e3;
    --navy: #14206a;
    --navy-deep: #0f1a58;
    --edge: #1ea8dc;
    --paper: #fbfbfa;
    --ink: #1a2870;
    --glow: #2aa7e0;
  }
  * { box-sizing: border-box; margin: 0; padding: 0; }
  html, body {
    width: 1200px; height: 716px; overflow: hidden;
    background: var(--backdrop);
    font-family: "Montserrat", Arial, sans-serif;
  }
  .stage {
    width: 1200px; height: 716px;
    display: flex; align-items: center; justify-content: center; gap: 40px;
  }
  .card {
    position: relative;
    width: 540px; height: 310px;
    border: 2px solid var(--edge);
    border-radius: 2px;
    box-shadow: 0 6px 18px rgba(0,0,0,.18);
  }

  /* Back side */
  .card--back {
    background: linear-gradient(160deg, var(--navy) 0%, var(--navy-deep) 100%);
    display: flex; align-items: center; justify-content: center; gap: 18px;
  }
  .card--back .mark-dot {
    width: 64px; height: 64px; border-radius: 50%;
    border: 3px solid var(--glow);
  }
  .card--back .brand-name {
    color: var(--glow);
    font-weight: 700; font-size: 22px; letter-spacing: .14em;
    text-transform: uppercase; line-height: 1.25;
  }

  /* Front side */
  .card--front { background: var(--paper); color: var(--ink); }
  .brand {
    position: absolute; right: 44px; top: 96px;
    display: flex; align-items: center; gap: 12px;
  }
  .brand .mark-dot {
    width: 52px; height: 52px; border-radius: 50%;
    background: var(--ink);
  }
  .brand .brand-name {
    color: var(--ink);
    font-weight: 700; font-size: 17px; letter-spacing: .12em;
    text-transform: uppercase; line-height: 1.2;
  }
  .contact {
    position: absolute; left: 34px; top: 132px;
    font-size: 11px; line-height: 1.45;
  }
  .contact__name { font-weight: 800; font-size: 19px; letter-spacing: .02em; text-transform: uppercase; line-height: 1.1; }
  .contact__role { font-weight: 500; margin-bottom: 10px; }
  .contact__address { margin-bottom: 8px; }
  .contact__line { display: flex; align-items: center; gap: 7px; }
  .contact__line svg { width: 10px; height: 10px; fill: var(--ink); flex: none; }
</style>
</head>
<body>
<main class="stage">
  <section class="card card--back" aria-label="Card back">
    <span class="mark-dot" aria-hidden="true"></span>
    <span class="brand-name">Wombarra<br>Devices</span>
  </section>

  <section class="card card--front" aria-label="Card front">
    <div class="brand">
      <span class="mark-dot" aria-hidden="true"></span>
      <span class="brand-name">Wombarra<br>Devices</span>
    </div>
    <div class="contact">
      <p class="contact__name">Dr Colin Harte</p>
      <p class="contact__role">R&amp;D Engineer</p>
      <p class="contact__address">PO Box XXX<br>Kelsby ACT 2917, Australia</p>
      <p class="contact__line">
        <svg viewBox="0 0 24 24" aria-hidden="true"><path d="M6.6 10.8a15.1 15.1 0 0 0 6.6 6.6l2.2-2.2a1 1 0 0 1 1-.25 11.4 11.4 0 0 0 3.6.57 1 1 0 0 1 1 1V20a1 1 0 0 1-1 1A17 17 0 0 1 3 4a1 1 0 0 1 1-1h3.5a1 1 0 0 1 1 1c0 1.25.2 2.45.57 3.57a1 1 0 0 1-.25 1z"/></svg>
        0427 563 710
      </p>
      <p class="contact__line">
        <svg viewBox="0 0 24 24" aria-hidden="true"><path d="M2 5h20v14H2zm2 2v.5l8 5 8-5V7zm0 2.8V17h16V9.8l-8 5z"/></svg>
        colin@wombarradevices.com.au
      </p>
    </div>
  </section>
</main>
</body>
</html>
```